Create an awesome website for a medical clinic

This is a new website for a doctor's office. The site should be clean and modern, easy to navigate.

This is a wellness clinic, we want to help our clients have a healthy, active lifestyle. It should be friendly and inviting, and easy for them to call or schedule an appointment.

The site should be responsive and designed using the attached Bootstrap 3 PSD.

We will provide stock photos, until then please use stock photos from:

pixelharbor.com or
framequarry.com (preferred)

Some example sites of clean and modern designs that we like:

https://tulsaspinecare.com/
http://reachpastjoints.com/
http://turninghealthier.com/

Also attached is a temporary logo you can use.

Reason: Thank you everyone for your great designs - we need a little more time so I'm extending the project.

Need extra days to review

Also, the colors in the new logo I just linked to are the final colors of the logo, so feel free to use any complimentary colors to it.

Hi everyone, The boss wants to change the layout of the site a little bit - here's the revised layout: https://www.filecrate.com/s/k9rt31vx2qp84zn/notes%2011_29_2017.pdf?dl=0 And the graphic assets you can use are here: https://www.filecrate.com/s/k9rt31vx2qp84zn/notes%2011_29_2017.pdf?dl=0 Feel free to change the background color of the "topbar", and change the icons of the "why people trust us" if you want, these are just temporary placeholders. Thanks for your patience and hard work!

Target Market(s)

People seeking medical treatment (wellness clinic)

Industry/Entity Type

Doctor

Number of Pages Required

1 page

Font styles to use
Sans Serif

Colors
0592cd
33a6d7
abd037
9bcb3c

Requirements
Must have
• The home page should have: a strong hero image/slideshow, clinic phone number should be prominent and at the top of the page (in the nav), a "what to expect" section (this is like a FAQs section - see attachment), and a strong call to action (a button to call or schedule an appointment).
• The what to expect section is useful so that prospective clients can determine if we're a good fit for them or not. It's a basic, first-step pre-qualification block of information.
• Social media icons which links to our social media profiles should be included.
Nice to have
• - Link to 3 most recent blog entries
• - Testimonials
• - How a multilevel nav menu looks.

```html
<!DOCTYPE html>
<html lang="en">
<head>
<meta charset="utf-8">
<title>Meadow Medical Clinic</title>
<link rel="stylesheet" href="https://fonts.googleapis.com/css2?family=Montserrat:wght@400;500&family=Ubuntu:wght@400;500;700&display=swap">
<style>
  :root {
    --blue: #0592cd;
    --blue-soft: #33a6d7;
    --green: #9bcb3c;
    --nav-bg: #1f1f1f;
    --nav-divider: #3a3a3a;
    --menu-bg: rgba(70, 66, 62, 0.88);
    --caption-bg: rgba(88, 72, 62, 0.72);
    --white: #ffffff;
    --ink: #4a4a4a;
    --page-bg: #ffffff;
  }
  * { box-sizing: border-box; margin: 0; padding: 0; }
  html, body { width: 1200px; height: 1200px; overflow: hidden; background: var(--page-bg); }
  body { position: relative; font-family: "Ubuntu", sans-serif; }

  .topbar {
    position: absolute; top: 0; left: 0; width: 1200px; height: 44px;
    background: var(--nav-bg); z-index: 5;
  }
  .main-nav { position: absolute; left: 345px; top: 0; display: flex; height: 44px; }
  .main-nav a {
    width: 134px; height: 44px; display: flex; align-items: center; justify-content: center;
    color: var(--white); font-size: 15px; font-weight: 500; text-decoration: none;
    border-left: 1px solid var(--nav-divider);
  }
  .main-nav a.is-active { border-bottom: 3px solid var(--blue-soft); }
  .nav-toggle { position: absolute; right: 14px; top: 12px; }

  .dropdown { position: absolute; left: 881px; top: 44px; width: 134px; z-index: 6; }
  .dropdown a, .dropdown-sub a {
    display: flex; justify-content: space-between; align-items: center;
    height: 35px; padding: 0 14px 0 22px; background: var(--menu-bg);
    color: #eee; font-size: 14px; text-decoration: none;
    border-bottom: 1px solid rgba(255,255,255,0.15);
  }
  .dropdown-sub { position: absolute; left: 1017px; top: 79px; width: 130px; z-index: 6; }

  .brand {
    position: absolute; left: 53px; top: 0; width: 260px; height: 186px; z-index: 7;
    background: var(--white);
    clip-path: polygon(0 0, 100% 0, 100% 86%, 50% 100%, 0 86%);
    text-align: center;
  }
  .brand-phone {
    display: flex; align-items: center; justify-content: center; gap: 8px;
    margin: 12px 18px 0; padding-bottom: 8px;
    border-bottom: 4px solid var(--blue);
    color: var(--blue); font-size: 21px; font-weight: 500;
  }
  .brand-name {
    margin-top: 20px; color: var(--blue);
    font-size: 24px; font-weight: 500; line-height: 1.3;
  }

  .hero {
    position: absolute; top: 44px; left: 0; width: 1200px; height: 716px;
  }
  .hero-photo {
    position: absolute; inset: 0;
    background:
      radial-gradient(ellipse at 40% 70%, #e8c3a6 0%, rgba(232,195,166,0) 45%),
      radial-gradient(ellipse at 85% 20%, #6b5142 0%, rgba(107,81,66,0) 50%),
      linear-gradient(160deg, #d9d2c8 0%, #c9a98f 40%, #b88a6c 65%, #e9e1cf 100%);
  }
  .hero-caption {
    position: absolute; left: 60px; top: 422px; width: 443px; height: 222px;
    background: var(--caption-bg); color: var(--white); text-align: center;
    font-family: "Montserrat", sans-serif;
  }
  .hero-caption h1 { font-weight: 400; font-size: 32px; margin-top: 14px; }
  .hero-caption hr { width: 140px; margin: 12px auto 10px; border: 0; border-top: 2px solid rgba(255,255,255,0.7); }
  .hero-caption p { font-size: 21px; line-height: 1.3; padding: 0 18px; }
  .btn-schedule {
    display: inline-block; margin-top: 14px; padding: 8px 12px;
    border: 2px solid rgba(255,255,255,0.85); border-radius: 5px;
    color: var(--white); font-family: "Ubuntu", sans-serif; font-size: 15px; font-weight: 500;
    text-decoration: none; letter-spacing: 0.3px;
  }
  .slider-dots { position: absolute; left: 560px; top: 680px; display: flex; gap: 10px; }
  .slider-dots span { width: 13px; height: 13px; border-radius: 50%; border: 2px solid rgba(255,255,255,0.85); }
  .slider-dots span.is-current { background: rgba(255,255,255,0.9); }

  .social-links { position: absolute; right: 40px; top: 674px; display: flex; gap: 10px; }
  .social-links a {
    width: 26px; height: 26px; border-radius: 50%;
    background: rgba(31,31,31,0.55); border: 2px solid rgba(255,255,255,0.85);
  }

  .expect { position: absolute; top: 760px; left: 0; width: 1200px; height: 440px; padding: 0 60px; }
  .expect h2 {
    text-align: center; color: var(--blue); font-weight: 400; font-size: 20px;
    margin: 22px auto 0; width: 460px; padding-bottom: 6px; border-bottom: 2px solid var(--blue-soft);
  }
  .expect-grid {
    margin-top: 22px; display: grid; grid-template-columns: repeat(4, 1fr);
    column-gap: 24px; row-gap: 20px;
  }
  .expect-text { height: 155px; font-size: 12px; color: var(--ink); line-height: 1.45; }
  .expect-text.align-right { text-align: right; }
  .expect-text.align-left { text-align: left; }
  .expect-text h3 { color: var(--blue-soft); font-size: 14px; font-weight: 500; line-height: 1.25; margin-bottom: 6px; }
  .expect-photo { height: 155px; }
  .photo-building { background: linear-gradient(180deg, #9fb8cf 0%, #c9d3da 45%, #7b8a72 100%); }
  .photo-reception { background: linear-gradient(150deg, #e7e4df 0%, #c8b3a2 50%, #9a6a45 100%); }
  .photo-care { background: linear-gradient(160deg, #d7dde2 0%, #b7a596 55%, #8d7a6c 100%); }
  .photo-doctor { background: linear-gradient(150deg, #eef2f5 0%, #cfdbe4 50%, #a9bccb 100%); }
</style>
</head>
<body>

<header class="topbar">
  <nav class="main-nav">
    <a href="#">Home</a>
    <a href="#">What to Expect</a>
    <a href="#">About</a>
    <a href="#">Blog</a>
    <a href="#" class="is-active">Testimonials</a>
    <a href="#">Contact</a>
  </nav>
  <svg class="nav-toggle" width="22" height="18" viewBox="0 0 22 18" aria-label="Menu">
    <rect y="0" width="22" height="3" fill="#fff"/>
    <rect y="7.5" width="22" height="3" fill="#fff"/>
    <rect y="15" width="22" height="3" fill="#fff"/>
  </svg>
</header>

<div class="dropdown">
  <a href="#">Submenu 1</a>
  <a href="#">Submenu 2 <span>›</span></a>
  <a href="#">Submenu 3</a>
</div>
<div class="dropdown-sub">
  <a href="#">Submenu 2.1</a>
  <a href="#">Submenu 2.2</a>
  <a href="#">Submenu 2.3</a>
</div>

<div class="brand">
  <div class="brand-phone">
    <svg width="22" height="18" viewBox="0 0 22 18" aria-hidden="true">
      <path d="M2 6 Q11 -1 20 6 L18 9 L15 7 L15 5 Q11 3 7 5 L7 7 L4 9 Z" fill="currentColor"/>
      <rect x="5" y="9" width="12" height="8" rx="1.5" fill="currentColor"/>
      <circle cx="11" cy="13" r="2" fill="#fff"/>
    </svg>
    555 - 014 - 2267
  </div>
  <div class="brand-name">Meadow<br>Medical Clinic</div>
</div>

<section class="hero">
  <div class="hero-photo" role="img" aria-label="Photo: therapist's hands giving a relaxing back massage to a client lying on a spa table with candles and flowers"></div>
  <div class="hero-caption">
    <h1>Lorem Ipsum Dolor</h1>
    <hr>
    <p>Dictumst consectetuer donec mi, vestibulum commodo eget nec in at viverra sociis bibendum.</p>
    <a href="#" class="btn-schedule">SCHEDULE NOW</a>
  </div>
  <div class="slider-dots"><span class="is-current"></span><span></span><span></span></div>
  <nav class="social-links" aria-label="Social media profiles">
    <a href="#" aria-label="Social profile 1"></a>
    <a href="#" aria-label="Social profile 2"></a>
    <a href="#" aria-label="Social profile 3"></a>
  </nav>
</section>

<section class="expect">
  <h2>What to Expect</h2>
  <div class="expect-grid">
    <div class="expect-text align-right">
      <h3>Headline 1<br>Example Text</h3>
      Lorem ipsum dolor sit amet, nunc convallis turpis a sed, sollicitudin quisque vel tellus proin, porta integer sapien dolor, suspendisse nulla vestibulum.
    </div>
    <div class="expect-photo photo-building" role="img" aria-label="Photo: modern clinic building exterior"></div>
    <div class="expect-photo photo-reception" role="img" aria-label="Photo: patient speaking with staff at the reception desk"></div>
    <div class="expect-text align-left">
      <h3>Headline 2<br>Example Text</h3>
      Aliquam nunc feugiat, mollis ligula etiam, sed ipsum luctus odio libero mi, turpis porta tortor, libero in lorem mauris elementum, tempus elit.
    </div>
    <div class="expect-text align-right">
      <h3>Headline 3<br>Example Text</h3>
      Blandit turpis a sed sollicitudin quisque vel tellus, proin porta integer sapien dolor, suspendisse nulla vestibulum, non nibh pharetra dolor semper.
    </div>
    <div class="expect-photo photo-care" role="img" aria-label="Photo: caregiver assisting an older patient"></div>
    <div class="expect-photo photo-doctor" role="img" aria-label="Photo: doctor consulting with a patient"></div>
    <div class="expect-text align-left">
      <h3>Headline 4<br>Example Text</h3>
      In massa egestas justo, libero nulla auctor sociis, suspendisse scelerisque nam ut, blandit lacinia non amet nulla, sed nonummy eu lacus.
    </div>
  </div>
</section>

</body>
</html>
```